KRWB new business card design

We need a business card design for our established business which is Australia wide however based in Melbourne. We are a young team of Financial Planners who specialize in Insurance and Basic super advice for people like us.

We are people who help our clients get things done in a timely and cost effective manner whilst having a good time and a laugh along the way.

We would like this to have a consistent feel with our new e-brochure which i have attached from a color and font perspective.

Industry/Entity Type

Business

Requirements
Must have
• We do not need specific address details rather just the states we are in:

VIC/NSW/QLD/TAS
Nice to have
• Curved edge to mate the brochure

```html
<!DOCTYPE html>
<html lang="en">
<head>
<meta charset="utf-8">
<title>KRWB business card concepts</title>
<link rel="stylesheet" href="https://fonts.googleapis.com/css2?family=Questrial&family=Arimo:wght@400;700&display=swap">
<style>
  :root {
    --stage: #b98a5e;
    --card: #050505;
    --green: #8cc63f;
    --green-deep: #1fa04a;
    --white: #ffffff;
    --soft: #d9d9d9;
    --photo-a: #6a6a6a;
    --photo-b: #2b2b2b;
  }
  * { box-sizing: border-box; margin: 0; padding: 0; }
  html, body { width: 1200px; height: 502px; overflow: hidden; }
  body {
    background: var(--stage);
    position: relative;
    font-family: "Questrial", "Century Gothic", sans-serif;
    color: var(--white);
  }
  .card {
    position: absolute;
    width: 354px;
    height: 203px;
    background: var(--card);
    border-bottom-right-radius: 30px;
    overflow: hidden;
  }
  .card--edged { border-right: 5px solid var(--green); }

  .brand {
    position: absolute;
    display: flex;
    align-items: center;
    gap: 8px;
    color: var(--green);
    font-family: "Questrial", sans-serif;
    letter-spacing: 2px;
    white-space: nowrap;
  }
  .brand__square { background: var(--green-deep); flex: none; }
  .brand--white { color: var(--white); }
  .brand--white .brand__square { background: var(--white); }

  .heading {
    font-weight: 700;
    letter-spacing: 2.4px;
    font-size: 13px;
    white-space: nowrap;
  }
  .services { list-style: none; font-size: 12.5px; color: var(--white); white-space: nowrap; }
  .services li::before { content: "\2022"; color: var(--green); margin-right: 5px; }
  .centered { position: absolute; left: 0; right: 0; text-align: center; }
  .divider { position: absolute; width: 1px; background: linear-gradient(transparent, var(--soft), transparent); }

  /* card 1: adviser details */
  .adviser__name { top: 10px; font-family: "Arimo", sans-serif; font-weight: 700; font-size: 13px; }
  .adviser__name em { font-weight: 400; font-size: 11px; }
  .adviser__role { top: 27px; font-family: "Arimo", sans-serif; font-size: 12px; }
  .contacts { position: absolute; left: 182px; top: 60px; list-style: none; font-family: "Arimo", sans-serif; font-size: 9.5px; line-height: 15.5px; }
  .contacts li { display: flex; align-items: center; gap: 5px; }
  .contacts svg { width: 8px; height: 8px; fill: var(--white); }
  .states { position: absolute; left: 182px; top: 139px; font-family: "Arimo", sans-serif; font-size: 10px; }
  .legal { top: 166px; font-family: "Arimo", sans-serif; font-size: 7.5px; line-height: 9px; }

  .photo {
    position: absolute; right: 0; top: 0; width: 52px; height: 203px;
    background: linear-gradient(180deg, var(--photo-a), var(--photo-b));
  }
  .columns { position: absolute; left: 14px; top: 166px; display: flex; font-size: 11px; line-height: 14px; white-space: nowrap; }
  .columns ul { list-style: none; padding: 0 8px 0 0; margin-right: 8px; border-right: 1px solid var(--green-deep); }
  .columns ul:last-child { border: 0; margin: 0; padding: 0; align-self: flex-end; }
  .columns li::before { content: "\2022"; color: var(--green); margin-right: 4px; }
</style>
</head>
<body>

  <!-- Card 1: adviser details -->
  <section class="card card--edged" style="left:35px;top:28px;">
    <p class="centered adviser__name">Daniel Hartley <em>ADFS, BBus, LRS&reg;</em></p>
    <p class="centered adviser__role">Financial Adviser</p>
    <div class="brand" style="left:76px;top:86px;font-size:20px;">
      <span class="brand__square" style="width:12px;height:12px;"></span>KRWB
    </div>
    <span class="divider" style="left:168px;top:58px;height:100px;"></span>
    <ul class="contacts">
      <li><svg viewBox="0 0 10 10"><path d="M2 0h2l1 3-1.5 1a6 6 0 0 0 2.5 2.5L7 5l3 1v2c0 1-1 2-2 2A8 8 0 0 1 0 2c0-1 1-2 2-2z"/></svg>1300 555 014</li>
      <li><svg viewBox="0 0 10 10"><rect x="2.5" y="0" width="5" height="10" rx="1"/></svg>0400 555 728</li>
      <li><svg viewBox="0 0 10 10"><path d="M0 4l2-2h6l2 2v5H0z"/></svg>03 9555 0192</li>
      <li><svg viewBox="0 0 10 10"><path d="M0 2h10v6H0z M0 2l5 4 5-4" /></svg>daniel@krwb.com.au</li>
      <li><svg viewBox="0 0 10 10"><circle cx="5" cy="5" r="5"/></svg>www.krwb.com.au</li>
    </ul>
    <p class="states">States:&nbsp; VIC/NSW/QLD/TAS</p>
    <p class="centered legal">KRWB Planning Pty Ltd<br>Authorised Representatives, Meridale Advice Group Limited<br>Australian Financial Services Licensee</p>
  </section>

  <!-- Card 2: services with team photo -->
  <section class="card card--edged" style="left:425px;top:28px;">
    <div class="brand" style="left:100px;top:45px;font-size:28px;">
      <span class="brand__square" style="width:16px;height:16px;"></span>KRWB
    </div>
    <p class="heading" style="position:absolute;left:84px;top:120px;">Specialising in:</p>
    <ul class="services" style="position:absolute;left:20px;top:140px;width:280px;text-align:center;line-height:19px;">
      <li style="display:inline">Risk Insurance</li>
      <li style="display:inline">Debt Management</li><br>
      <li style="display:inline">Superannuation</li><br>
      <li style="display:inline">Wealth Creation</li>
      <li style="display:inline">Retirement Planning</li>
    </ul>
    <div class="photo" role="img" aria-label="Portrait photo of a smiling team member"></div>
  </section>

  <!-- Card 3: services in columns -->
  <section class="card" style="left:816px;top:31px;height:205px;">
    <div class="brand" style="left:130px;top:50px;font-size:30px;">
      <span class="brand__square" style="width:16px;height:16px;"></span>KRWB
    </div>
    <p class="heading" style="position:absolute;left:113px;top:140px;">Specialising in:</p>
    <div class="columns">
      <ul><li>Risk Insurance</li><li>Debt Management</li></ul>
      <ul><li>Superannuation</li><li>Wealth Creation</li></ul>
      <ul><li>Retirement Planning</li></ul>
    </div>
  </section>

  <!-- Card 4: white mark with web address -->
  <section class="card" style="left:38px;top:274px;height:206px;">
    <div class="brand brand--white" style="left:130px;top:55px;font-size:30px;">
      <span class="brand__square" style="width:16px;height:16px;"></span>KRWB
    </div>
    <p class="centered heading" style="top:131px;">Specialising in:</p>
    <p class="centered" style="top:151px;font-size:12.5px;line-height:18px;">
      &bull; Risk Insurance &bull; Debt Management &bull; Superannuation<br>
      &bull; Wealth Creation &bull; Retirement Planning
    </p>
    <p class="centered" style="top:186px;font-size:12px;letter-spacing:3px;">www.krwb.com.au</p>
  </section>

  <!-- Card 5: mark left, list right -->
  <section class="card card--edged" style="left:432px;top:274px;height:201px;">
    <div class="brand" style="left:40px;top:85px;font-size:28px;">
      <span class="brand__square" style="width:16px;height:16px;"></span>KRWB
    </div>
    <span class="divider" style="left:174px;top:40px;height:120px;"></span>
    <p class="heading" style="position:absolute;left:190px;top:44px;">Specialising in:</p>
    <ul class="services" style="position:absolute;left:190px;top:72px;line-height:21px;">
      <li>Risk Insurance</li><li>Debt Management</li><li>Superannuation</li><li>Wealth Creation</li><li>Retirement Planning</li>
    </ul>
  </section>

  <!-- Card 6: list left, mark right -->
  <section class="card" style="left:818px;top:278px;height:205px;">
    <p class="heading" style="position:absolute;left:26px;top:32px;font-size:15px;">Specialising in:</p>
    <ul class="services" style="position:absolute;left:26px;top:56px;font-size:15px;line-height:25px;">
      <li>Risk Insurance</li><li>Debt Management</li><li>Superannuation</li><li>Wealth Creation</li><li>Retirement Planning</li>
    </ul>
    <div class="brand" style="left:222px;top:88px;font-size:28px;">
      <span class="brand__square" style="width:14px;height:14px;"></span>KRWB
    </div>
  </section>

</body>
</html>
```